KDWB Business Card

Looking for a business card design to incorporate our branding. We want to only use the colors listing in the Branding Package (attached).
Updates

Target Market(s)

People who need their phone or device fixed.

Industry/Entity Type

Electronics

Contact Information for Business Card

Please use:

Brightwick Gadget Clinic LLC
4810 E Harlow Ridge Rd
Suite 417
San Antonio, TX 78163

Marcus Delgrove, Store Manager

(210) 555-0147

Requirements
Must have
• Must include the colors that are contained within the Branding Package PDF file.

```html
<!DOCTYPE html>
<html lang="en">
<head>
<meta charset="utf-8">
<title>Brightwick Gadget Clinic – Business Card</title>
<link href="https://fonts.googleapis.com/css2?family=Arimo:wght@400;700&display=swap" rel="stylesheet">
<style>
  :root {
    --page-bg: #e9e7e4;
    --card-black: #1c1c1c;
    --card-white: #ffffff;
    --brand-orange: #f05a22;
    --slate-grey: #58595b;
    --ink: #222222;
    --on-dark: #ffffff;
  }
  * { box-sizing: border-box; margin: 0; padding: 0; }
  html, body {
    width: 1200px; height: 810px; overflow: hidden;
    background: var(--page-bg);
    font-family: "Arimo", Arial, sans-serif;
  }
  .sheet {
    position: relative; width: 1200px; height: 810px;
  }
  .card {
    position: absolute; top: 250px;
    width: 540px; height: 309px;
    border-radius: 16px; overflow: hidden;
    box-shadow: 0 6px 18px rgba(0,0,0,0.18);
  }
  .card--back { left: 40px; background: var(--card-black); }
  .card--front { left: 620px; background: var(--card-white); }

  .brand {
    position: absolute; display: flex; align-items: center; gap: 12px;
  }
  .brand__mark {
    width: 34px; height: 34px; background: var(--brand-orange);
  }
  .brand__name {
    color: var(--brand-orange); font-size: 26px; font-weight: 400;
    letter-spacing: 0.2px; white-space: nowrap;
  }
  .card--back .brand {
    left: 50%; top: 50%; transform: translate(-50%, -50%);
  }
  .card--front .brand { left: 34px; top: 40px; }
  .card--front .brand__name { font-size: 24px; }

  .card__shapes { position: absolute; inset: 0; width: 100%; height: 100%; }

  .person {
    position: absolute; right: 30px; top: 96px; text-align: right;
  }
  .person__name { font-size: 22px; color: var(--ink); font-weight: 400; }
  .person__role { font-size: 13px; color: var(--brand-orange); margin-top: 2px; }

  .contact {
    position: absolute; left: 24px; top: 168px;
    list-style: none; color: var(--on-dark); font-size: 12.5px;
  }
  .contact li { display: flex; align-items: center; gap: 10px; margin-bottom: 11px; }
  .icon { width: 14px; height: 14px; flex: none; }

  .address {
    position: absolute; right: 26px; top: 196px;
    display: flex; align-items: flex-start; gap: 10px;
    color: var(--on-dark); font-size: 14px; line-height: 1.35; text-align: right;
  }
  .address .icon { margin-top: 18px; }
</style>
</head>
<body>
<main class="sheet">
  <section class="card card--back" aria-label="Card back">
    <div class="brand">
      <span class="brand__mark"></span>
      <span class="brand__name">Brightwick Gadget Clinic</span>
    </div>
  </section>

  <section class="card card--front" aria-label="Card front">
    <svg class="card__shapes" viewBox="0 0 540 309" preserveAspectRatio="none" aria-hidden="true">
      <polygon points="0,146 283,146 297,309 0,309" fill="var(--slate-grey)"/>
      <polygon points="289,146 540,146 540,309 303,309" fill="var(--brand-orange)"/>
    </svg>

    <div class="brand">
      <span class="brand__mark"></span>
      <span class="brand__name">Brightwick Gadget Clinic</span>
    </div>

    <div class="person">
      <p class="person__name">Marcus Delgrove</p>
      <p class="person__role">Store Manager</p>
    </div>

    <ul class="contact">
      <li>
        <svg class="icon" viewBox="0 0 14 14" aria-hidden="true"><rect width="14" height="14" fill="#fff"/><path d="M4 3c1 0 1.5 2 1 2.5L4.6 6c.6 1.3 1.6 2.3 2.9 2.9l.6-.6c.5-.4 2.5.1 2.5 1.1 0 1-1 1.8-2 1.6C6 10.4 3.6 8 3 5c-.2-1 .5-2 1-2z" fill="var(--slate-grey)"/></svg>
        <span>(210) 555-0147</span>
      </li>
      <li>
        <svg class="icon" viewBox="0 0 14 14" aria-hidden="true"><rect width="14" height="14" fill="#fff"/><rect x="2.5" y="4" width="9" height="6.5" fill="none" stroke="var(--slate-grey)" stroke-width="1.2"/><path d="M2.5 4l4.5 3.6L11.5 4" fill="none" stroke="var(--slate-grey)" stroke-width="1.2"/></svg>
        <span>marcus@BrightwickGadget.com</span>
      </li>
      <li>
        <svg class="icon" viewBox="0 0 14 14" aria-hidden="true"><rect width="14" height="14" fill="#fff"/><circle cx="7" cy="7" r="4.2" fill="none" stroke="var(--slate-grey)" stroke-width="1.2"/><path d="M2.8 7h8.4M7 2.8c-2 2.5-2 5.9 0 8.4M7 2.8c2 2.5 2 5.9 0 8.4" fill="none" stroke="var(--slate-grey)" stroke-width="1"/></svg>
        <span>www.BrightwickGadget.com</span>
      </li>
    </ul>

    <div class="address">
      <p>4810 E Harlow Ridge Rd<br>Suite 417<br>San Antonio, TX 78163</p>
      <svg class="icon" viewBox="0 0 14 14" aria-hidden="true"><rect width="14" height="14" fill="#fff"/><path d="M7 2.5a3 3 0 0 1 3 3c0 2.2-3 5.8-3 5.8S4 7.7 4 5.5a3 3 0 0 1 3-3z" fill="var(--brand-orange)"/><circle cx="7" cy="5.5" r="1.1" fill="#fff"/></svg>
    </div>
  </section>
</main>
</body>
</html>
```